1876 Basins & Spouts Business Card

I'm wanting to get a business card designed. Our business is 1876 Basins & Spouts
Details for the card:

1876 Basins & Spouts
Name: Harold Vesk
Email: harold@1876basinsandspouts.com.au
Website: www.1876basinsandspouts.com.au
Mobile: 0438 260 947
Phone: 02 7481 3926

Font of Basins & Spouts is called Snell Roundhand. Not sue what font logo text is.

I'm thinking two sided but it doesn't have to be.

```html
<!DOCTYPE html>
<html lang="en">
<head>
<meta charset="utf-8">
<title>1876 Basins &amp; Spouts – Business Card</title>
<link rel="stylesheet" href="https://fonts.googleapis.com/css2?family=Lato:wght@300;400&family=Poppins:wght@600&display=swap">
<style>
  :root {
    --bg: #d6d5d1;
    --ink: #050608;
    --paper: #ffffff;
    --stripe: #6b6b6b;
    --muted: #5a5a5a;
    --rule: #c4c4c4;
  }
  * { box-sizing: border-box; margin: 0; padding: 0; }
  html, body { width: 1200px; height: 801px; overflow: hidden; }
  body {
    background: var(--bg);
    font-family: "Lato", sans-serif;
    position: relative;
  }
  .card {
    position: absolute;
    top: 245px;
    width: 540px;
    height: 310px;
    overflow: hidden;
  }
  .card--front { left: 40px; background: var(--paper); }
  .card--back { left: 620px; background: var(--ink); color: var(--paper); }

  .front-swoosh { position: absolute; inset: 0; width: 540px; height: 310px; }

  .brand {
    position: absolute;
    display: flex;
    align-items: center;
    gap: 10px;
  }
  .brand__dot {
    border-radius: 50%;
    border: 1.5px solid currentColor;
    flex: none;
  }
  .brand__name { font-weight: 400; white-space: nowrap; }
  .brand__tagline { font-weight: 300; white-space: nowrap; }

  .card--front .brand { left: 240px; top: 78px; color: var(--ink); }
  .card--front .brand__dot { width: 34px; height: 34px; }
  .card--front .brand__name { font-size: 19px; line-height: 1.1; }
  .card--front .brand__tagline { font-size: 8px; margin-top: 3px; }

  .address {
    position: absolute;
    right: 40px;
    top: 128px;
    text-align: right;
    color: var(--muted);
    font-size: 13px;
    line-height: 1.4;
    font-weight: 400;
    font-style: normal;
  }

  .divider {
    position: absolute;
    left: 40px;
    top: 188px;
    width: 460px;
    height: 1px;
    background: var(--rule);
  }
  .divider::before {
    content: "";
    position: absolute;
    left: 0; top: 0;
    width: 130px; height: 1px;
    background: var(--ink);
  }

  .person-name {
    position: absolute;
    left: 40px;
    top: 160px;
    font-family: "Poppins", sans-serif;
    font-weight: 600;
    font-size: 19px;
    line-height: 1.2;
    color: var(--ink);
  }

  .contact-list {
    position: absolute;
    left: 40px;
    top: 198px;
    list-style: none;
  }
  .contact-list li {
    display: flex;
    align-items: center;
    gap: 10px;
    height: 23px;
    font-size: 13px;
    font-weight: 300;
    color: var(--muted);
  }
  .contact-list svg { width: 11px; height: 11px; flex: none; }

  .card--back .brand { left: 110px; top: 108px; }
  .card--back .brand__dot { width: 60px; height: 60px; }
  .card--back .brand__name { font-size: 25px; line-height: 1.1; }
  .card--back .brand__tagline { font-size: 10px; margin-top: 4px; }
  .back-footer {
    position: absolute;
    left: 0; right: 0;
    top: 238px;
    text-align: center;
    font-size: 13px;
    font-weight: 400;
  }
</style>
</head>
<body>

<section class="card card--front" aria-label="Business card front">
  <svg class="front-swoosh" viewBox="0 0 540 310" aria-hidden="true">
    <path d="M0,0 H540 V10 C380,14 170,30 0,92 Z" fill="var(--ink)"/>
    <path d="M540,14 C380,20 200,40 70,110 C200,46 380,26 540,22 Z" fill="var(--stripe)"/>
  </svg>

  <div class="brand">
    <span class="brand__dot" aria-hidden="true"></span>
    <div>
      <div class="brand__name">1876 Basins &amp; Spouts</div>
      <div class="brand__tagline">Heritage craft shaped for the way you live today</div>
    </div>
  </div>

  <address class="address">Harlow Crossing<br>Denmere Vale, 1742</address>

  <h1 class="person-name">Harold Vesk</h1>
  <div class="divider" aria-hidden="true"></div>

  <ul class="contact-list">
    <li>
      <svg viewBox="0 0 12 12" aria-hidden="true"><path d="M2.5 1 L4.5 1 L5 3.5 L3.8 4.4 C4.5 6 6 7.5 7.6 8.2 L8.5 7 L11 7.5 L11 9.5 C11 10.3 10.3 11 9.5 11 C5 10.8 1.2 7 1 2.5 C1 1.7 1.7 1 2.5 1 Z" fill="var(--ink)"/></svg>
      02 7481 3926
    </li>
    <li>
      <svg viewBox="0 0 12 12" aria-hidden="true"><rect x="3" y="0.8" width="6" height="10.4" rx="1" fill="none" stroke="var(--ink)" stroke-width="1.2"/><circle cx="6" cy="9.4" r="0.6" fill="var(--ink)"/></svg>
      0438 260 947
    </li>
    <li>
      <svg viewBox="0 0 12 12" aria-hidden="true"><rect x="0.8" y="2" width="10.4" height="8" fill="var(--ink)"/><path d="M3 5.5 L5.2 7.5 L9.5 3.5" fill="none" stroke="var(--paper)" stroke-width="1.3"/></svg>
      harold@1876basinsandspouts.com.au
    </li>
    <li>
      <svg viewBox="0 0 12 12" aria-hidden="true"><circle cx="6" cy="6" r="5" fill="var(--ink)"/><path d="M1 6 H11 M6 1 C3.5 3.5 3.5 8.5 6 11 M6 1 C8.5 3.5 8.5 8.5 6 11" fill="none" stroke="var(--paper)" stroke-width="0.7"/></svg>
      www.1876basinsandspouts.com.au
    </li>
  </ul>
</section>

<section class="card card--back" aria-label="Business card back">
  <div class="brand">
    <span class="brand__dot" aria-hidden="true"></span>
    <div>
      <div class="brand__name">1876 Basins &amp; Spouts</div>
      <div class="brand__tagline">Heritage craft shaped for the way you live today</div>
    </div>
  </div>
  <p class="back-footer">1876 Basins &amp; Spouts</p>
</section>

</body>
</html>
```